Talon Microsystems PowerPoint Master Slide Deck Design

This is a 2-phase project to design a slide deck for a semiconductor company in the Silicon Valley. The design budget will be increased with each phase.
The slide deck will need to have one version with a dark background for presentations and a second version with a white background. Otherwise, the slides will be the same. I anticipate we will need a total of 10 slides, but that number may change.
The first phase will be to design a Title and a Title and Content slide.
- The Title Slide is the first slide of the deck. It should include the presentation title, the presenter's name and date of presentation
- The Title and Content slide should include a title and content with bullet points and up to 2 additional sub-bullets
- The Title and Content slide should have a footer that includes the slide #, Talon Microsystems Confidential, and the logo. This footer will be on every slide except the Title Slide
The first two slides will serve as the format for the remaining ~8 slides:
-Header and Content Text (1, 2, 4 column)
-Header and Content Image (bar chart, pie chart, tables)
-Break
-Title only
-Closing (Talon logo only)
Our slides contain a lot of content so a clean and simple design is best.
Both phases will need to include pre-set color options for
-Text and Lines
-Shadows
-Bullets and sub-bullets (including shapes, ex. circle, slash, square, etc.)
-Bar charts, pie charts, tables
Samples of our collateral are attached. Logo files are also attached
Look and feel
Each slider illustrates characteristics of the customer's brand and the style your logo design should communicate.

```html
<!DOCTYPE html>
<html lang="en">
<head>
<meta charset="utf-8">
<title>Talon Microsystems Slide Master – Light and Dark</title>
<link href="https://fonts.googleapis.com/css2?family=Roboto:wght@400;500;700&display=swap" rel="stylesheet">
<style>
  :root{
    --page:#eef0f0;
    --sheet:#ffffff;
    --blue:#1336f2;
    --cyan:#00c6f7;
    --ink:#111111;
    --muted:#444a52;
    --accent-line:#12b4ee;
    --bar-track:#dcdcdc;
    --bar-1:#0ba885;
    --bar-2:#1d7bc2;
    --bar-3:#17baa0;
    --bar-4:#1796c6;
    --bar-5:#0b2cf0;
    --dark-bg:#000000;
  }
  *{box-sizing:border-box;margin:0;padding:0}
  html,body{width:811px;height:1200px;overflow:hidden}
  body{background:var(--page);font-family:'Roboto',Arial,sans-serif;position:relative}

  .sheet{position:absolute;top:29px;width:345px;height:1141px;background:var(--sheet);border:1px solid #cfd3d6}
  .sheet.left{left:43px}
  .sheet.right{left:423px}

  .slide{position:absolute;left:25px;width:293px;height:165px;overflow:hidden;
    --text:var(--ink);--body:var(--muted);--bg:#fff;--logo:#0d1b3e;--footer:linear-gradient(180deg,var(--cyan),var(--blue));
    background:var(--bg);color:var(--text);box-shadow:0 0.5px 2px rgba(0,0,0,.18)}
  .dark .slide{--text:#fff;--body:#e6e8ec;--bg:var(--dark-bg);--logo:#fff;--footer:var(--cyan)}
  .s1{top:27px}.s2{top:211px}.s3{top:396px}.s4{top:580px}.s5{top:765px}.s6{top:950px}

  /* header */
  .slide-title{position:absolute;left:13px;top:11px;font-size:10.5px;font-weight:500;letter-spacing:-.1px}
  .title-rule{position:absolute;left:0;top:27px;width:32px;height:0.6px;background:var(--accent-line)}
  .title-rule::after{content:"";position:absolute;right:-1px;top:-0.7px;width:2px;height:2px;border-radius:50%;background:var(--accent-line)}
  .brand{position:absolute;right:10px;top:11px;display:flex;align-items:center;gap:3px;color:var(--logo);font-size:8.5px;font-weight:500;letter-spacing:.3px}
  .brand i{width:6px;height:6px;border-radius:50%;background:var(--cyan);display:block}

  /* footer */
  .footer{position:absolute;left:0;top:147px;width:259px;height:14px;background:var(--footer);color:#fff;font-size:3.8px;border-radius:0 7px 7px 0}
  .footer .date{position:absolute;left:8px;top:5px}
  .footer .conf{position:absolute;left:90px;top:5px}
  .footer .mini{position:absolute;left:209px;top:4.2px;font-size:4.6px;font-weight:700;display:flex;align-items:center;gap:1.5px}
  .footer .mini i{width:3px;height:3px;border-radius:50%;background:#fff;display:block}
  .footer .num{position:absolute;right:1.5px;top:1.5px;width:11px;height:11px;border-radius:50%;background:#fff;color:#111;border:0.6px solid var(--blue);font-size:3.6px;display:flex;align-items:center;justify-content:center}

  /* title slide */
  .cover{color:#fff;text-align:center}
  .cover .photo{position:absolute;inset:0;background:linear-gradient(165deg,#1a6cf5 0%,#12b8f4 45%,#0b2df0 100%)}
  .dark .cover .photo{background:linear-gradient(165deg,#2a2c31 0%,#3a3d43 45%,#1b1c20 100%)}
  .cover .brand{left:13px;right:auto;top:12px;color:#fff;font-size:12px;font-weight:500}
  .cover .brand i{background:#fff;width:9px;height:9px}
  .cover .welcome{position:absolute;left:0;right:0;top:54px;font-size:9px}
  .cover h1{position:absolute;left:0;right:0;top:66px;font-size:20px;font-weight:700;letter-spacing:-.1px}
  .cover .rule{position:absolute;left:116px;top:90px;width:62px;height:1px;background:#fff}
  .cover .presenter{position:absolute;left:0;right:0;top:96px;font-size:7.8px}
  .cover .when{position:absolute;left:0;right:0;top:109px;font-size:6.2px}

  /* features */
  .bullets{position:absolute;left:13px;top:36px;width:262px;list-style:none}
  .bullets>li{position:relative;padding-left:5px;font-size:4.5px;font-weight:700;line-height:7.3px}
  .bullets>li::before{content:"";position:absolute;left:0;top:2px;border-left:2.6px solid var(--blue);border-top:1.7px solid transparent;border-bottom:1.7px solid transparent}
  .dark .bullets>li::before{border-left-color:var(--cyan)}
  .bullets ul{list-style:none;margin:2px 0 3px 7px}
  .bullets ul li{position:relative;padding-left:4px;font-size:3.9px;font-weight:400;color:var(--body);line-height:7.5px}
  .bullets ul li::before{content:"";position:absolute;left:0;top:3px;width:1.5px;height:1.5px;border-radius:50%;background:var(--cyan)}

  /* about */
  .image-box{position:absolute;left:12px;top:37px;width:116px;height:101px;background:radial-gradient(ellipse at 45% 55%,#4ad9d6 0%,#1e6f7c 35%,#0e2f3b 75%,#081a22 100%)}
  .prose{position:absolute;font-size:4.3px;line-height:6.9px;color:var(--body)}
  .prose p+p{margin-top:6px}
  .about-text{left:146px;top:39px;width:137px}
  .col-a{left:12px;top:36px;width:132px}
  .col-b{left:157px;top:36px;width:126px}
  .works-text{left:12px;top:38px;width:117px}

  /* chart */
  .chart{position:absolute;left:138px;top:41px;width:146px;list-style:none}
  .chart li{position:relative;height:10px;margin-bottom:8.7px}
  .chart .idx{position:absolute;left:0;top:-0.5px;font-size:10px;font-weight:500;color:var(--text)}
  .dark .chart .idx{display:none}
  .chart .track{position:absolute;left:16px;top:0;width:128px;height:10px;border-radius:5px;background:var(--bar-track)}
  .chart .fill{position:absolute;left:0;top:0;height:10px;border-radius:0 5px 5px 0;color:#fff;font-size:5.6px;text-align:right;padding-right:11px;line-height:10px}
  .chart .fill::after{content:"";position:absolute;right:2px;top:2px;width:6px;height:6px;border-radius:50%;background:#fff}
  .chart .fill::before{content:"";position:absolute;right:3.5px;top:3.5px;width:3px;height:3px;border-radius:50%;background:currentColor;opacity:0}

  /* closing */
  .closing .backdrop{position:absolute;inset:0;background:linear-gradient(160deg,#0f6cf4 0%,#0fb9f6 40%,#0b2ef0 100%)}
  .dark .closing .backdrop{background:radial-gradient(ellipse at 40% 55%,#1f2b36 0%,#101820 55%,#070b10 100%)}
  .closing .mark{position:absolute;left:0;right:0;top:52px;display:flex;align-items:center;justify-content:center;gap:9px;color:#fff}
  .closing .mark i{width:26px;height:26px;border-radius:50%;background:#fff;display:block}
  .closing .mark span{font-size:24px;font-weight:500;line-height:28px;letter-spacing:.5px}
</style>
</head>
<body>

<!-- light deck -->
<section class="sheet left">
  <div class="slide cover s1">
    <div class="photo" role="img" aria-label="Gloved hand holding a microchip under a blue tint"></div>
    <div class="brand"><i></i>TALON</div>
    <p class="welcome">Welcome To</p>
    <h1>Talon Microsystems</h1>
    <div class="rule"></div>
    <p class="presenter">The Presenter's Name: Maya Orlen</p>
    <p class="when">13/12/2023</p>
  </div>

  <div class="slide s2">
    <h2 class="slide-title">Our Features</h2><div class="title-rule"></div>
    <div class="brand"><i></i>TALON</div>
    <ul class="bullets">
      <li>Lorem ipsum dolor sit amet, consectetur adipiscing elit, sed do eiusmod tempor incididunt ut labore et dolore magna aliqua.
        <ul>
          <li>Excepteur sint occaecat cupidatat non proident, sunt in deserunt mollit anim id est laborum.</li>
          <li>Nemo enim ipsam aut odit aut fugit, sed quia eos qui ratione voluptatem sequi nesciunt.</li>
          <li>Sed ut perspiciatis unde omnis iste natus error sit voluptatem accusantium.</li>
        </ul>
      </li>
      <li>Duis aute irure dolor in reprehenderit in voluptate velit esse cillum dolore eu fugiat nulla pariatur.
        <ul>
          <li>Nemo enim ipsam voluptatem quia voluptas sit aut odit aut fugit, sed quia eos qui ratione nesciunt.</li>
          <li>Sed ut perspiciatis unde omnis iste natus error sit voluptatem accusantium.</li>
          <li>Ut enim ad minima veniam, quis nostrum exercitationem ullam corporis suscipit laboriosam.</li>
          <li>Nemo enim ipsam aut odit aut fugit, sed quia eos qui ratione voluptatem sequi nesciunt.</li>
          <li>Nemo enim ipsam voluptatem quia voluptas sit aut odit aut fugit, sed quia eos qui ratione nesciunt.</li>
        </ul>
      </li>
    </ul>
    <footer class="footer"><span class="date">13/12/2023</span><span class="conf">Talon Microsystems Confidential</span><span class="mini"><i></i>TALON</span><span class="num">02</span></footer>
  </div>

  <div class="slide s3">
    <h2 class="slide-title">About Us</h2><div class="title-rule"></div>
    <div class="brand"><i></i>TALON</div>
    <div class="image-box" role="img" aria-label="Close-up of a glowing processor chip on a circuit board"></div>
    <div class="prose about-text">
      <p>Nemo enim ipsam voluptatem quia voluptas sit aspernatur aut odit aut fugit, sed quia consequuntur magni dolores eos qui ratione voluptatem sequi nesciunt. Neque porro quisquam est, qui dolorem ipsum quia dolor sit amet, consectetur, adipisci velit, sed quia non numquam eius modi tempora incidunt ut labore et dolore magnam aliquam quaerat voluptatem.</p>
      <p>Lorem ipsum dolor sit amet, consectetur adipiscing elit, sed do eiusmod tempor incididunt ut labore et dolore magna aliqua. Ut enim ad minim veniam, quis nostrud exercitation ullamco laboris nisi ut aliquip ex ea commodo consequat. Duis aute irure dolor in reprehenderit in voluptate velit esse cillum dolore eu fugiat nulla pariatur. Excepteur sint occaecat cupidatat non proident, sunt in culpa qui officia deserunt mollit anim id est laborum.</p>
    </div>
    <footer class="footer"><span class="date">13/12/2023</span><span class="conf">Talon Microsystems Confidential</span><span class="mini"><i></i>TALON</span><span class="num">03</span></footer>
  </div>

  <div class="slide s4">
    <h2 class="slide-title">Why Choose Us</h2><div class="title-rule"></div>
    <div class="brand"><i></i>TALON</div>
    <div class="prose col-a">
      <p>Lorem ipsum dolor sit amet, consectetur adipiscing elit, sed do eiusmod tempor incididunt ut labore et dolore magna aliqua. Ut enim ad minim veniam, quis nostrud exercitation ullamco nisi ut aliquip ex ea commodo consequat. Duis aute irure dolor in voluptate velit esse cillum dolore eu fugiat nulla pariatur.</p>
      <p>Sed ut perspiciatis unde omnis iste natus error sit voluptatem accusantium doloremque laudantium, totam rem aperiam, eaque ipsa quae ab illo inventore veritatis et quasi architecto beatae vitae dicta sunt explicabo. Nemo enim ipsam quia voluptas sit aspernatur aut odit aut fugit, sed quia magni dolores eos qui ratione voluptatem sequi nesciunt.</p>
      <p>Excepteur sint occaecat cupidatat non proident, sunt in culpa qui officia deserunt mollit anim id est laborum.</p>
    </div>
    <div class="prose col-b">
      <p>Ut enim ad minima veniam, quis nostrum exercitationem ullam corporis suscipit laboriosam, nisi ut aliquid ex ea. Quis autem vel eum iure reprehenderit qui in ea voluptate velit esse quam nihil molestiae consequatur, vel illum qui dolorem eum fugiat quo voluptas nulla pariatur?</p>
      <p>Neque porro quisquam est, qui dolorem ipsum quia dolor sit amet, consectetur, adipisci velit, sed quia non numquam eius modi tempora incidunt ut labore et dolore magnam aliquam quaerat voluptatem. Duis aute irure dolor in reprehenderit in voluptate velit esse cillum dolore eu fugiat nulla pariatur.</p>
      <p>Ut enim ad minim veniam, quis nostrud exercitation ullamco laboris nisi ut aliquip ex ea commodo consequat.</p>
    </div>
    <footer class="footer"><span class="date">13/12/2023</span><span class="conf">Talon Microsystems Confidential</span><span class="mini"><i></i>TALON</span><span class="num">04</span></footer>
  </div>

  <div class="slide s5">
    <h2 class="slide-title">How Talon Microsystems Works</h2><div class="title-rule"></div>
    <div class="brand"><i></i>TALON</div>
    <div class="prose works-text">
      <p>Ut enim ad minima veniam, quis nostrum exercitationem ullam corporis suscipit laboriosam, nisi ut aliquid ex ea. Quis autem vel eum iure reprehenderit qui in ea voluptate velit esse quam nihil molestiae consequatur, vel illum qui dolorem eum fugiat quo voluptas nulla pariatur?</p>
      <p>Neque porro quisquam est, qui dolorem ipsum quia dolor sit amet, consectetur, adipisci velit, sed quia non numquam eius modi tempora incidunt ut labore et magnam aliquam quaerat voluptatem. Duis aute irure dolor in reprehenderit in voluptate velit esse cillum dolore eu fugiat nulla pariatur.</p>
    </div>
    <ul class="chart">
      <li><span class="idx">01</span><span class="track"><span class="fill" style="width:80%;background:var(--bar-1)">80%</span></span></li>
      <li><span class="idx">02</span><span class="track"><span class="fill" style="width:65%;background:var(--bar-2)">65%</span></span></li>
      <li><span class="idx">03</span><span class="track"><span class="fill" style="width:90%;background:var(--bar-3)">90%</span></span></li>
      <li><span class="idx">04</span><span class="track"><span class="fill" style="width:85%;background:var(--bar-4)">85%</span></span></li>
      <li><span class="idx">05</span><span class="track"><span class="fill" style="width:100%;background:var(--bar-5);border-radius:5px">100%</span></span></li>
    </ul>
    <footer class="footer"><span class="date">13/12/2023</span><span class="conf">Talon Microsystems Confidential</span><span class="mini"><i></i>TALON</span><span class="num">05</span></footer>
  </div>

  <div class="slide closing s6">
    <div class="backdrop"></div>
    <div class="mark"><i></i><span>TALON<br>Microsystems</span></div>
  </div>
</section>

<!-- dark deck -->
<section class="sheet right dark">
  <div class="slide cover s1">
    <div class="photo" role="img" aria-label="Gloved hand holding a microchip in low light"></div>
    <div class="brand"><i></i>TALON</div>
    <p class="welcome">Welcome To</p>
    <h1>Talon Microsystems</h1>
    <div class="rule"></div>
    <p class="presenter">The Presenter's Name: Maya Orlen</p>
    <p class="when">13/12/2023</p>
  </div>

  <div class="slide s2">
    <h2 class="slide-title">Our Features</h2><div class="title-rule"></div>
    <div class="brand"><i></i>TALON</div>
    <ul class="bullets">
      <li>Lorem ipsum dolor sit amet, consectetur adipiscing elit, sed do eiusmod tempor incididunt ut labore et dolore magna aliqua.
        <ul>
          <li>Excepteur sint occaecat cupidatat non proident, sunt in deserunt mollit anim id est laborum.</li>
          <li>Nemo enim ipsam aut odit aut fugit, sed quia eos qui ratione voluptatem sequi nesciunt.</li>
          <li>Sed ut perspiciatis unde omnis iste natus error sit voluptatem accusantium.</li>
        </ul>
      </li>
      <li>Duis aute irure dolor in reprehenderit in voluptate velit esse cillum dolore eu fugiat nulla pariatur.
        <ul>
          <li>Nemo enim ipsam voluptatem quia voluptas sit aut odit aut fugit, sed quia eos qui ratione nesciunt.</li>
          <li>Sed ut perspiciatis unde omnis iste natus error sit voluptatem accusantium.</li>
          <li>Ut enim ad minima veniam, quis nostrum exercitationem ullam corporis suscipit laboriosam.</li>
          <li>Nemo enim ipsam aut odit aut fugit, sed quia eos qui ratione voluptatem sequi nesciunt.</li>
          <li>Nemo enim ipsam voluptatem quia voluptas sit aut odit aut fugit, sed quia eos qui ratione nesciunt.</li>
        </ul>
      </li>
    </ul>
    <footer class="footer"><span class="date">13/12/2023</span><span class="conf">Talon Microsystems Confidential</span><span class="mini"><i></i>TALON</span><span class="num">02</span></footer>
  </div>

  <div class="slide s3">
    <h2 class="slide-title">About Us</h2><div class="title-rule"></div>
    <div class="brand"><i></i>TALON</div>
    <div class="image-box" role="img" aria-label="Close-up of a glowing processor chip on a circuit board"></div>
    <div class="prose about-text">
      <p>Nemo enim ipsam voluptatem quia voluptas sit aspernatur aut odit aut fugit, sed quia consequuntur magni dolores eos qui ratione voluptatem sequi nesciunt. Neque porro quisquam est, qui dolorem ipsum quia dolor sit amet, consectetur, adipisci velit, sed quia non numquam eius modi tempora incidunt ut labore et dolore magnam aliquam quaerat voluptatem.</p>
      <p>Lorem ipsum dolor sit amet, consectetur adipiscing elit, sed do eiusmod tempor incididunt ut labore et dolore magna aliqua. Ut enim ad minim veniam, quis nostrud exercitation ullamco laboris nisi ut aliquip ex ea commodo consequat. Duis aute irure dolor in reprehenderit in voluptate velit esse cillum dolore eu fugiat nulla pariatur. Excepteur sint occaecat cupidatat non proident, sunt in culpa qui officia deserunt mollit anim id est laborum.</p>
    </div>
    <footer class="footer"><span class="date">13/12/2023</span><span class="conf">Talon Microsystems Confidential</span><span class="mini"><i></i>TALON</span><span class="num">03</span></footer>
  </div>

  <div class="slide s4">
    <h2 class="slide-title">Why Choose Us</h2><div class="title-rule"></div>
    <div class="brand"><i></i>TALON</div>
    <div class="prose col-a">
      <p>Lorem ipsum dolor sit amet, consectetur adipiscing elit, sed do eiusmod tempor incididunt ut labore et dolore magna aliqua. Ut enim ad minim veniam, quis nostrud exercitation ullamco nisi ut aliquip ex ea commodo consequat. Duis aute irure dolor in voluptate velit esse cillum dolore eu fugiat nulla pariatur.</p>
      <p>Sed ut perspiciatis unde omnis iste natus error sit voluptatem accusantium doloremque laudantium, totam rem aperiam, eaque ipsa quae ab illo inventore veritatis et quasi architecto beatae vitae dicta sunt explicabo. Nemo enim ipsam quia voluptas sit aspernatur aut odit aut fugit, sed quia magni dolores eos qui ratione voluptatem sequi nesciunt.</p>
      <p>Excepteur sint occaecat cupidatat non proident, sunt in culpa qui officia deserunt mollit anim id est laborum.</p>
    </div>
    <div class="prose col-b">
      <p>Ut enim ad minima veniam, quis nostrum exercitationem ullam corporis suscipit laboriosam, nisi ut aliquid ex ea. Quis autem vel eum iure reprehenderit qui in ea voluptate velit esse quam nihil molestiae consequatur, vel illum qui dolorem eum fugiat quo voluptas nulla pariatur?</p>
      <p>Neque porro quisquam est, qui dolorem ipsum quia dolor sit amet, consectetur, adipisci velit, sed quia non numquam eius modi tempora incidunt ut labore et dolore magnam aliquam quaerat voluptatem. Duis aute irure dolor in reprehenderit in voluptate velit esse cillum dolore eu fugiat nulla pariatur.</p>
      <p>Ut enim ad minim veniam, quis nostrud exercitation ullamco laboris nisi ut aliquip ex ea commodo consequat.</p>
    </div>
    <footer class="footer"><span class="date">13/12/2023</span><span class="conf">Talon Microsystems Confidential</span><span class="mini"><i></i>TALON</span><span class="num">04</span></footer>
  </div>

  <div class="slide s5">
    <h2 class="slide-title">How Talon Microsystems Works</h2><div class="title-rule"></div>
    <div class="brand"><i></i>TALON</div>
    <div class="prose works-text">
      <p>Ut enim ad minima veniam, quis nostrum exercitationem ullam corporis suscipit laboriosam, nisi ut aliquid ex ea. Quis autem vel eum iure reprehenderit qui in ea voluptate velit esse quam nihil molestiae consequatur, vel illum qui dolorem eum fugiat quo voluptas nulla pariatur?</p>
      <p>Neque porro quisquam est, qui dolorem ipsum quia dolor sit amet, consectetur, adipisci velit, sed quia non numquam eius modi tempora incidunt ut labore et magnam aliquam quaerat voluptatem. Duis aute irure dolor in reprehenderit in voluptate velit esse cillum dolore eu fugiat nulla pariatur.</p>
    </div>
    <ul class="chart">
      <li><span class="idx">01</span><span class="track"><span class="fill" style="width:80%;background:var(--bar-1)">80%</span></span></li>
      <li><span class="idx">02</span><span class="track"><span class="fill" style="width:65%;background:var(--bar-2)">65%</span></span></li>
      <li><span class="idx">03</span><span class="track"><span class="fill" style="width:90%;background:var(--bar-3)">90%</span></span></li>
      <li><span class="idx">04</span><span class="track"><span class="fill" style="width:85%;background:var(--bar-4)">85%</span></span></li>
      <li><span class="idx">05</span><span class="track"><span class="fill" style="width:100%;background:var(--bar-5);border-radius:5px">100%</span></span></li>
    </ul>
    <footer class="footer"><span class="date">13/12/2023</span><span class="conf">Talon Microsystems Confidential</span><span class="mini"><i></i>TALON</span><span class="num">05</span></footer>
  </div>

  <div class="slide closing s6">
    <div class="backdrop" role="img" aria-label="Dark close-up of a circuit board with a chip"></div>
    <div class="mark"><i></i><span>TALON<br>Microsystems</span></div>
  </div>
</section>

</body>
</html>
```